Federal Government Proposal Development Consulting company needs a website designed and coded

I am looking for someone to design (using an existing logo, color palette, and text fonts) and code a wordpress-based website for a Proposal Development consulting company. I have full copy for all site pages and suggestions for images/ graphics and a few example design templates to go from.

One note, from a color perspective - I included a mockup of a business card to highlight a color scheme that I tend to like - if you look at the back of the business card, the blend of the grey, blue, with the neon green highlight as a separator really seems to pop. Just a thought as you are designing the page.

I would like to see 2-3 potential design layouts, and I will select one to move forward with. Then, I would like the site to be coded for WordPress (I can provide a login to my wordpress site). I would like 1 opportunity to review the coded site and make any final tweaks.

```html
<!DOCTYPE html>
<html lang="en">
<head>
<meta charset="utf-8">
<title>Clearquill Consulting LLC — Proposal Development Support</title>
<link href="https://fonts.googleapis.com/css2?family=Fondamento&family=Montserrat:wght@400;500;600;700&display=swap" rel="stylesheet">
<style>
:root{
  --navy:#0b0c4a;
  --royal:#0a40c8;
  --royal-soft:#2e5ee0;
  --ice:#e9fbfd;
  --ink:#222233;
  --body:#444455;
  --muted:#8a8a99;
  --line:#d9dbe3;
  --white:#ffffff;
  --display:"Fondamento", serif;
  --sans:"Montserrat", sans-serif;
}
*{box-sizing:border-box;margin:0;padding:0}
html,body{width:1200px;height:4651px;overflow:hidden}
body{position:relative;background:var(--white);font-family:var(--sans);color:var(--body)}
.abs{position:absolute}
a{color:inherit;text-decoration:none}

/* hero */
.hero{left:0;top:0;width:1200px;height:720px;background:var(--navy);overflow:hidden}
.hero-art{left:0;top:0;width:1200px;height:720px}
.brand{left:143px;top:18px;color:var(--white);font-family:var(--display);font-size:25px;line-height:1}
.brand small{display:block;font-size:10px;margin-left:38px;margin-top:2px;opacity:.9}
.nav{left:365px;top:28px;display:flex;gap:38px;font-size:11.5px;color:var(--white);letter-spacing:.3px;font-weight:500}
.hero h1{left:143px;top:190px;width:520px;font-family:var(--display);font-weight:400;font-size:31px;line-height:44px;letter-spacing:-.4px;color:var(--white);white-space:nowrap}
.hero .lead{left:143px;top:386px;width:480px;font-size:20px;line-height:29px;color:var(--white)}
.hero .lead b{font-weight:700}
.btn-outline{left:143px;top:467px;width:330px;height:39px;border:1.5px solid var(--white);border-radius:20px;color:var(--white);font-size:11px;display:flex;align-items:center;padding-left:32px;gap:14px;letter-spacing:.2px}
.btn-outline i{width:17px;height:17px;border-radius:50%;background:#9fe8f2;display:inline-flex;align-items:center;justify-content:center;margin-left:auto;margin-right:18px}

.section-title{font-family:var(--display);font-weight:400;color:var(--navy);font-size:36px;line-height:1}
.center{text-align:center;width:1200px;left:0}

/* what we do */
.intro{left:199px;top:810px;width:803px;text-align:center;font-size:12.3px;line-height:23px;color:var(--body)}
.intro p+p{margin-top:12px}
.card{width:283px;height:433px;top:1020px;background:var(--white);border-radius:14px;box-shadow:0 4px 18px rgba(20,30,80,.13);padding:64px 32px 0 32px}
.card .ico{position:absolute;left:28px;top:-2px;width:56px;height:56px;border-radius:50%;background:var(--royal);display:flex;align-items:center;justify-content:center}
.card h3{font-family:var(--display);font-weight:400;font-size:15px;color:var(--ink);padding-bottom:12px;border-bottom:1px solid var(--line);margin-bottom:14px}
.card p{font-size:11.4px;line-height:17.8px;color:var(--body)}
.card p+p{margin-top:12px}

/* who we are */
.who-bg{left:0;top:1550px;width:1200px;height:830px}
.who-photo{left:143px;top:1715px;width:444px;height:502px;border-radius:0 70px 0 0;background:linear-gradient(160deg,#e8ecef 0%,#b9c2ca 55%,#6b6560 100%)}
.who-title{left:623px;top:1763px}
.who-text{left:623px;top:1826px;width:435px;font-size:11.8px;line-height:23.2px}
.btn{height:34px;border-radius:17px;background:var(--royal);color:var(--white);font-size:11px;display:flex;align-items:center;justify-content:center;letter-spacing:.3px}

/* services */
.services{left:186px;top:2496px;width:825px;display:grid;grid-template-columns:repeat(5,153px);column-gap:15px;row-gap:20px}
.svc{height:124px;background:var(--white);box-shadow:0 2px 12px rgba(20,30,80,.12);display:flex;flex-direction:column;align-items:center;justify-content:flex-end;padding-bottom:18px;text-align:center;font-size:12.5px;line-height:15px;color:var(--ink)}
.svc svg{margin-bottom:8px}
.svc.active{background:var(--royal);color:var(--white);font-weight:600}

/* expertise */
.sme-list{left:143px;top:3160px;list-style:none}
.sme-list li{display:flex;align-items:center;gap:17px;height:35.8px;font-size:13.5px;color:var(--ink)}
.sme-photo{left:614px;top:3079px;width:444px;height:504px;border-radius:60px 0 60px 0;background:linear-gradient(140deg,#4a3a2b 0%,#8a7157 40%,#c5c9cf 60%,#6e5a45 100%)}

/* contact */
.city{left:0;top:3640px;width:1200px;height:580px}
.contact-card{left:148px;top:3881px;width:904px;height:473px;background:var(--white);border-radius:14px;box-shadow:0 6px 24px rgba(20,30,80,.15)}
.contact-panel{left:170px;top:3902px;width:337px;height:430px;background:var(--royal);border-radius:10px;color:var(--white);padding:40px 36px}
.contact-panel h2{font-family:var(--display);font-weight:400;font-size:34px;line-height:1;margin-bottom:30px}
.contact-panel .sub{font-size:11.4px;line-height:18px;margin-bottom:22px}
.cinfo{display:flex;gap:12px;margin-bottom:20px;font-size:12px;line-height:20px}
.cinfo b{display:block;font-weight:700;font-size:11.5px;line-height:16px}
.social{display:flex;gap:10px;margin-top:6px}
.social span{width:26px;height:26px;border:1.5px solid var(--white);border-radius:50%}
.form-title{left:536px;top:3944px}
.field{width:232px}
.field label{display:block;font-size:9.5px;color:var(--muted)}
.field .val{font-size:12px;color:var(--ink);padding:6px 0 12px;border-bottom:1px solid var(--line)}
.msg{left:536px;top:4158px;width:488px}
.msg .val{height:90px}

/* footer */
.foot-brand{top:4453px;color:#6b6b80;font-family:var(--display);font-size:32px;line-height:1}
.foot-brand small{display:block;font-size:13px;margin-top:2px}
.foot-nav{top:4566px;display:flex;justify-content:center;gap:22px;font-size:11.5px;color:var(--ink)}
.foot-nav span.sep{color:var(--muted)}
.legal{left:143px;top:4621px;width:917px;display:flex;justify-content:space-between;font-size:11px;color:var(--ink)}
</style>
</head>
<body>

<!-- HERO -->
<section class="hero abs">
  <svg class="hero-art abs" viewBox="0 0 1200 720" aria-hidden="true">
    <path d="M740 0 C660 110 650 330 760 450 C830 530 960 560 1200 560 L1200 0 Z" fill="#1b35b8"/>
    <path d="M800 0 C720 120 720 320 820 430 C900 510 1030 530 1200 520 L1200 0 Z" fill="#e7fbfd"/>
    <circle cx="667" cy="440" r="52" fill="#1b35b8"/>
    <path d="M0 672 C220 600 420 640 620 660 C850 684 1000 640 1200 660 L1200 720 L0 720 Z" fill="#ffffff"/>
  </svg>
  <div class="abs" role="img" aria-label="Photo of two colleagues reviewing work on a laptop" style="left:760px;top:110px;width:440px;height:540px;border-radius:180px 0 0 0;background:linear-gradient(160deg,#f3f6f8 0%,#c9d2dc 35%,#1f2c55 70%,#15214a 100%)"></div>
  <div class="brand abs">Clearquill<small>Consulting LLC</small></div>
  <nav class="nav abs"><a>HOME</a><a>WORK WITH US</a><a>WORK FOR US</a><a>ABOUT US</a><a>CONTACT US</a></nav>
  <h1 class="abs">Trying To Convey That We Provide<br>Proposal Development Support &amp;<br>Have A Technical Background To<br>Win Contracts.</h1>
  <p class="lead abs"><b>Generate Success</b>: Fuel Innovation in Proposal Excellence with Clearquill!</p>
  <a class="btn-outline abs">CLICK HERE TO EXPLORE OUR SERVICES <i><svg width="9" height="9" viewBox="0 0 10 10"><path d="M1.5 5.2 L4 7.5 L8.5 2.5" fill="none" stroke="#0b0c4a" stroke-width="1.8"/></svg></i></a>
</section>

<!-- WHAT WE DO -->
<h2 class="section-title abs center" style="top:745px">What We Do</h2>
<div class="intro abs">
  <p>Clearquill, specializes in advancing an organization through a comprehensive suite of services designed to modernize the proposal development process. From innovative Capture Management strategies that pinpoint lucrative opportunities, meticulous Proposal Development services that transform concepts into effective narratives, and cutting-edge Generative AI techniques that create domain-aware content accelerating proposal draft development, we are your dedicated partner in securing success. With a unique fusion of technical expertise and exceptional writing capabilities, we surpass industry standards and set new benchmarks for excellence.</p>
  <p>Discover a dynamic approach to proposal consulting that goes beyond conventional boundaries—choose Clearquill for solutions that <b>Enhance</b> the quality of your work, <b>Elevate</b> your corporate advantage, and <b>Expand</b> your industry presence.</p>
</div>

<article class="card abs" style="left:143px">
  <span class="ico"><svg width="28" height="28" viewBox="0 0 28 28" fill="none" stroke="#fff" stroke-width="1.6"><rect x="7" y="7" width="14" height="14" rx="2"/><path d="M11 3v4M17 3v4M11 21v4M17 21v4M3 11h4M3 17h4M21 11h4M21 17h4"/></svg></span>
  <h3>Generative AI</h3>
  <p>Revolutionize your proposal writing process with our domain-aware Generative AI services. Using customer-installed tools, we leverage domain-aware artificial intelligence to generate innovative and tailored proposal content. This not only accelerates the proposal development timeline but also ensures content that is both dynamic and targeted.</p>
  <p>Stay ahead of the curve with proposals that not only meet industry standards but exceed expectations, thanks to the creative insights generated by our AI-driven approach.</p>
</article>
<article class="card abs" style="left:457px">
  <span class="ico"><svg width="28" height="28" viewBox="0 0 28 28" fill="none" stroke="#fff" stroke-width="1.6"><circle cx="12" cy="12" r="7"/><path d="M17 17l7 7"/><path d="M9 12h6M12 9v6"/></svg></span>
  <h3>Capture Management</h3>
  <p>Elevate your business development strategy with our Capture Management services. From opportunity identification to strategic planning, our experts will guide you through a meticulous process, ensuring the pursuit of the right contracts to position your organization for success.</p>
  <p>Trust us to analyze the market, mitigate risks, and develop strategies that maximize the ability to secure lucrative opportunities.</p>
</article>
<article class="card abs" style="left:773px">
  <span class="ico"><svg width="28" height="28" viewBox="0 0 28 28" fill="none" stroke="#fff" stroke-width="1.6"><rect x="6" y="3" width="16" height="22" rx="2"/><path d="M10 9h8M10 14h8M10 19h5"/></svg></span>
  <h3>Proposal Development</h3>
  <p>Transform your vision into winning proposals with our Proposal Development services. We specialize in persuasive narratives, clear technical solutions, and strategic pricing models. From meticulous compliance reviews to captivating executive summaries, we ensure every aspect of a proposal is polished and aligned with your objectives.</p>
  <p>Turn your ideas into persuasive documents that leave a lasting impression on clients to set you apart from the competition.</p>
</article>

<!-- WHO WE ARE -->
<svg class="who-bg abs" viewBox="0 0 1200 830" aria-hidden="true">
  <path d="M0 55 C120 20 280 20 500 45 L1200 45 L1200 760 C1000 690 800 700 600 730 C400 760 200 760 0 740 Z" fill="var(--ice)"/>
  <path d="M0 55 C110 18 260 8 500 45 C330 40 150 40 0 66 Z" fill="var(--navy)"/>
  <path d="M700 760 C880 700 1050 690 1200 740 L1200 820 C1080 760 900 740 700 760 Z" fill="var(--navy)"/>
</svg>
<div class="who-photo abs" role="img" aria-label="Photo of two businessmen talking at a meeting table with a laptop"></div>
<h2 class="section-title abs who-title">Who We Are</h2>
<div class="who-text abs">
  <p>It is a long established fact that a reader will be distracted by the readable content of a page when looking at its layout. The point of using Lorem Ipsum is that it has a more-or-less normal distribution of letters, as opposed to using 'Content here, content here', making it look like readable English. Many are desktop publishing packages and web page editors now use Lorem Ipsum as their default model text, and a search for 'lorem ipsum' will uncover many web sites still in their infancy.</p>
  <p>There are many variations of passages of Lorem Ipsum available, but the majority have suffered alteration in some form, by injected humour, or other randomised words which don't look even slightly believable.</p>
</div>
<a class="btn abs" style="left:623px;top:2132px;width:140px">ABOUT US</a>

<!-- SERVICES -->
<h2 class="section-title abs center" style="top:2428px">Our Services</h2>
<div class="services abs">
  <div class="svc active"><svg width="38" height="38" viewBox="0 0 38 38" fill="none" stroke="#fff" stroke-width="1.5"><rect x="11" y="11" width="16" height="16" rx="2"/><path d="M15 5v6M23 5v6M15 27v6M23 27v6M5 15h6M5 23h6M27 15h6M27 23h6"/></svg>Generative<br>AI</div>
  <div class="svc"><svg width="38" height="38" viewBox="0 0 38 38" fill="none" stroke="#222" stroke-width="1.4"><circle cx="22" cy="12" r="6"/><path d="M20 18v3h4v-3M5 28h9l6-4h8M5 24v8"/></svg>Technical<br>Solutioning</div>
  <div class="svc"><svg width="38" height="38" viewBox="0 0 38 38" fill="none" stroke="#222" stroke-width="1.4"><path d="M12 32v-8c-4-3-5-9-1-14 4-4 12-4 15 1 2 3 2 6 1 8l2 4h-3v5h-5v4"/></svg>Competitive<br>Intelligence</div>
  <div class="svc"><svg width="38" height="38" viewBox="0 0 38 38" fill="none" stroke="#222" stroke-width="1.4"><circle cx="16" cy="15" r="9"/><path d="M22 22l9 9"/><circle cx="16" cy="13" r="3"/><path d="M11 20c1-3 9-3 10 0"/></svg>Capture<br>Management</div>
  <div class="svc"><svg width="38" height="38" viewBox="0 0 38 38" fill="none" stroke="#222" stroke-width="1.4"><rect x="9" y="5" width="20" height="28" rx="2"/><path d="M13 12h12M13 17h12M13 22h12M13 27h7"/></svg>Proposal<br>Management</div>

  <div class="svc"><svg width="38" height="38" viewBox="0 0 38 38" fill="none" stroke="#222" stroke-width="1.4"><rect x="10" y="4" width="18" height="20" rx="1"/><path d="M14 10h10M14 14h10M14 18h6M7 31l2-3 2 3M17 31l2-3 2 3M27 31l2-3 2 3"/></svg>Compliance<br>Reviews</div>
  <div class="svc"><svg width="38" height="38" viewBox="0 0 38 38" fill="none" stroke="#222" stroke-width="1.4"><circle cx="15" cy="14" r="8"/><circle cx="24" cy="23" r="8"/><path d="M12 14h6M21 23h6"/></svg>Executive<br>Summaries</div>
  <div class="svc"><svg width="38" height="38" viewBox="0 0 38 38" fill="none" stroke="#222" stroke-width="1.4"><path d="M8 15h5l7-6v20l-7-6H8z"/><path d="M25 13c3 3 3 9 0 12M29 9c5 5 5 15 0 20"/></svg>Volume<br>Lead</div>
  <div class="svc"><svg width="38" height="38" viewBox="0 0 38 38" fill="none" stroke="#222" stroke-width="1.4"><circle cx="18" cy="8" r="4"/><path d="M12 33V18c0-3 3-5 6-5s6 2 6 5v15M15 24h6"/></svg>Technical<br>Writer</div>
  <div class="svc"><svg width="38" height="38" viewBox="0 0 38 38" fill="none" stroke="#222" stroke-width="1.4"><rect x="6" y="7" width="26" height="24" rx="1"/><path d="M19 7v24M10 13h6M10 18h6M10 23h6M22 13h6M22 18h6M22 23h6"/></svg>Book<br>Boss</div>

  <div class="svc"><svg width="38" height="38" viewBox="0 0 38 38" fill="none" stroke="#222" stroke-width="1.4"><rect x="7" y="5" width="20" height="28" rx="1"/><path d="M11 11h12M11 16h12M11 21h8M22 29l10-14 2 2-10 14z"/></svg>Resume<br>Writer</div>
  <div class="svc"><svg width="38" height="38" viewBox="0 0 38 38" fill="none" stroke="#222" stroke-width="1.4"><rect x="5" y="6" width="28" height="20" rx="1"/><path d="M15 26v5h8v-5M11 31h16"/></svg>Desktop<br>Publishing</div>
  <div class="svc"><svg width="38" height="38" viewBox="0 0 38 38" fill="none" stroke="#222" stroke-width="1.4"><rect x="11" y="4" width="20" height="26" rx="1"/><path d="M7 9v25h20M15 10h12M15 15h12M15 20h12M15 25h8"/></svg>Proposal<br>Production</div>
  <div class="svc"><svg width="38" height="38" viewBox="0 0 38 38" fill="none" stroke="#222" stroke-width="1.4"><path d="M9 4h14l7 7v23H9z"/><path d="M23 4v7h7M13 17h13M13 22h13M13 27h9"/></svg>Templates &amp;<br>Processes</div>
  <div class="svc"><svg width="38" height="38" viewBox="0 0 38 38" fill="none" stroke="#222" stroke-width="1.4"><rect x="9" y="6" width="20" height="27" rx="1"/><path d="M15 4h8v4h-8zM13 14l2 2 3-3M13 22l2 2 3-3M21 15h5M21 23h5"/></svg>Market<br>Survey</div>
</div>
<a class="btn abs" style="left:529px;top:2951px;width:141px">READ MORE</a>

<!-- SUBJECT MATTER EXPERTISE -->
<h2 class="section-title abs" style="left:143px;top:3088px">Subject Matter Expertise</h2>
<ul class="sme-list abs">
  <li><svg width="17" height="17" viewBox="0 0 17 17"><circle cx="8.5" cy="8.5" r="7.5" fill="none" stroke="#2e5ee0" stroke-width="1.3"/><path d="M5 8.7l2.4 2.3 4.6-4.8" fill="none" stroke="#2e5ee0" stroke-width="1.4"/></svg>Generative AI</li>
  <li><svg width="17" height="17" viewBox="0 0 17 17"><circle cx="8.5" cy="8.5" r="7.5" fill="none" stroke="#2e5ee0" stroke-width="1.3"/><path d="M5 8.7l2.4 2.3 4.6-4.8" fill="none" stroke="#2e5ee0" stroke-width="1.4"/></svg>Software/ Hardware Engineering</li>
  <li><svg width="17" height="17" viewBox="0 0 17 17"><circle cx="8.5" cy="8.5" r="7.5" fill="none" stroke="#2e5ee0" stroke-width="1.3"/><path d="M5 8.7l2.4 2.3 4.6-4.8" fill="none" stroke="#2e5ee0" stroke-width="1.4"/></svg>Systems Engineering</li>
  <li><svg width="17" height="17" viewBox="0 0 17 17"><circle cx="8.5" cy="8.5" r="7.5" fill="none" stroke="#2e5ee0" stroke-width="1.3"/><path d="M5 8.7l2.4 2.3 4.6-4.8" fill="none" stroke="#2e5ee0" stroke-width="1.4"/></svg>High-Performance Computing (HPC)</li>
  <li><svg width="17" height="17" viewBox="0 0 17 17"><circle cx="8.5" cy="8.5" r="7.5" fill="none" stroke="#2e5ee0" stroke-width="1.3"/><path d="M5 8.7l2.4 2.3 4.6-4.8" fill="none" stroke="#2e5ee0" stroke-width="1.4"/></svg>Secure Supply Chain (ISO 28000 &amp; ISO 20243-1)</li>
  <li><svg width="17" height="17" viewBox="0 0 17 17"><circle cx="8.5" cy="8.5" r="7.5" fill="none" stroke="#2e5ee0" stroke-width="1.3"/><path d="M5 8.7l2.4 2.3 4.6-4.8" fill="none" stroke="#2e5ee0" stroke-width="1.4"/></svg>Logistics, Warehousing</li>
  <li><svg width="17" height="17" viewBox="0 0 17 17"><circle cx="8.5" cy="8.5" r="7.5" fill="none" stroke="#2e5ee0" stroke-width="1.3"/><path d="M5 8.7l2.4 2.3 4.6-4.8" fill="none" stroke="#2e5ee0" stroke-width="1.4"/></svg>Information Technology Support</li>
  <li><svg width="17" height="17" viewBox="0 0 17 17"><circle cx="8.5" cy="8.5" r="7.5" fill="none" stroke="#2e5ee0" stroke-width="1.3"/><path d="M5 8.7l2.4 2.3 4.6-4.8" fill="none" stroke="#2e5ee0" stroke-width="1.4"/></svg>Cybersecurity</li>
  <li><svg width="17" height="17" viewBox="0 0 17 17"><circle cx="8.5" cy="8.5" r="7.5" fill="none" stroke="#2e5ee0" stroke-width="1.3"/><path d="M5 8.7l2.4 2.3 4.6-4.8" fill="none" stroke="#2e5ee0" stroke-width="1.4"/></svg>Data Analysis</li>
  <li><svg width="17" height="17" viewBox="0 0 17 17"><circle cx="8.5" cy="8.5" r="7.5" fill="none" stroke="#2e5ee0" stroke-width="1.3"/><path d="M5 8.7l2.4 2.3 4.6-4.8" fill="none" stroke="#2e5ee0" stroke-width="1.4"/></svg>Systems Integration</li>
  <li><svg width="17" height="17" viewBox="0 0 17 17"><circle cx="8.5" cy="8.5" r="7.5" fill="none" stroke="#2e5ee0" stroke-width="1.3"/><path d="M5 8.7l2.4 2.3 4.6-4.8" fill="none" stroke="#2e5ee0" stroke-width="1.4"/></svg>Program Management</li>
  <li><svg width="17" height="17" viewBox="0 0 17 17"><circle cx="8.5" cy="8.5" r="7.5" fill="none" stroke="#2e5ee0" stroke-width="1.3"/><path d="M5 8.7l2.4 2.3 4.6-4.8" fill="none" stroke="#2e5ee0" stroke-width="1.4"/></svg>Systems Development &amp; Testing</li>
</ul>
<div class="sme-photo abs" role="img" aria-label="Photo of a laptop showing a bar chart on a wooden desk beside a coffee cup"></div>

<!-- CONTACT -->
<svg class="city abs" viewBox="0 0 1200 580" role="img" aria-label="Photo of a city skyline with high-rise towers at dusk">
  <defs><linearGradient id="cityTone" x1="0" y1="0" x2="0" y2="1"><stop offset="0" stop-color="#3a4a66"/><stop offset=".6" stop-color="#4a4f5e"/><stop offset="1" stop-color="#8a6e55"/></linearGradient></defs>
  <path d="M0 40 C250 0 500 -10 750 30 C950 60 1100 40 1200 20 L1200 480 C1000 560 700 580 500 560 C300 545 150 520 0 540 Z" fill="url(#cityTone)"/>
  <path d="M0 40 C200 8 420 0 620 22 C400 25 200 40 0 70 Z" fill="var(--navy)"/>
  <path d="M0 540 C150 520 300 545 500 560 C300 560 120 570 0 590 Z" fill="var(--navy)"/>
</svg>
<div class="contact-card abs"></div>
<div class="contact-panel abs">
  <h2>Contact Us</h2>
  <p class="sub">Lorem ipsum is simply dummy text of the printing and typesetting industry.</p>
  <div class="cinfo"><svg width="14" height="18" viewBox="0 0 14 18"><path d="M7 1a6 6 0 0 0-6 6c0 4.5 6 10 6 10s6-5.5 6-10a6 6 0 0 0-6-6z" fill="#fff"/><circle cx="7" cy="7" r="2.2" fill="#0a40c8"/></svg><div><b>Address</b>123 Building Name, Street,<br>Harrow Falls, Avalon</div></div>
  <div class="cinfo"><svg width="15" height="15" viewBox="0 0 16 16"><path d="M3 1l3 3-1.5 2.5c1 2 3 4 5 5L12 10l3 3-2 2C7 15 1 9 1 3z" fill="#fff"/></svg><div><b>Phone</b>123 456 7890</div></div>
  <div class="cinfo"><svg width="15" height="12" viewBox="0 0 15 12"><rect x=".5" y=".5" width="14" height="11" rx="1" fill="#fff"/><path d="M1 1l6.5 5.5L14 1" fill="none" stroke="#0a40c8" stroke-width="1.2"/></svg><div><b>Email</b>inquiry@clearquill-proposals.com</div></div>
  <div class="social" aria-label="Social media links"><span></span><span></span><span></span><span></span></div>
</div>
<h2 class="section-title abs form-title">Get In Touch</h2>
<div class="field abs" style="left:536px;top:4004px"><label>Name</label><div class="val">Lorem ipsum</div></div>
<div class="field abs" style="left:792px;top:4004px"><label>Email Address</label><div class="val">info@clearquill-proposals.com</div></div>
<div class="field abs" style="left:536px;top:4089px"><label>Company Name</label><div class="val">Lorem ipsum</div></div>
<div class="field abs" style="left:792px;top:4089px"><label>Phone Number</label><div class="val">123-456-7890</div></div>
<div class="field msg abs"><label>Message</label><div class="val">Your Message is here</div></div>
<a class="btn abs" style="left:536px;top:4301px;width:141px">SEND NOW</a>

<!-- FOOTER -->
<div class="foot-brand abs center">Clearquill<small>Consulting LLC</small></div>
<nav class="foot-nav abs center"><a>HOME</a><span class="sep">|</span><a>WORK WITH US</a><span class="sep">|</span><a>WORK FOR US</a><span class="sep">|</span><a>ABOUT US</a><span class="sep">|</span><a>CONTACT US</a></nav>
<div class="legal abs"><span>© 2024 Clearquill. All Rights Reserved.</span><span>Privacy Policy &nbsp;&nbsp;|&nbsp;&nbsp; Terms &amp; Conditions</span></div>

</body>
</html>
```